Web Design Project

Website Design Brief

Company Details
1a) Name of Company

MAPLEHAVEN
1) What is the nature of your business?: Briefly describe your products or services:

INDEPENDENT CONTEMPORARY TRADITIONAL ITALIAN RESTAURANT IN THE HEART OF ELMSWORTH QUAY ALSO CATERING FOR PRIVATE CORPORATE EVENTS AND WEDDING RECEPTIONS

1a) Who is your target market? Who are you hoping to reach with your site?

CITY CORPORATES, LOCAL CORPORATES/BUSINESSES, LOCAL RESIDENTS, VISITORS TO THE DOCK, LOCAL HOTELS

Website Details
1b) Do you have an existing website? If so, what is the URL?
HTTP://WWW.MAPLEHAVENTRATTORIA.EXAMPLE

2b) IMPORTANT: Please list at least 3 URLs (web addresses) of high quality sites that you like the look of (these do not have to be sites who’s business is similar to yours. It aids us in determining what your design style is.) Please consider layout, colours, navigation, graphics, and typography.

http://www.thecorvelle.example/

http://www.dunmorrow.example/

http://www.pavokitchen.example/

http://www.ilfaro.example/

3b) What colours or colour schemes would you like?

WHITE, BLACK, SILVER/ALUMINIUM (PLS LOOK AT OUR OUTSIDE CHAIRS)

4b) List the Navigation links for your Site:

5b) What type of look are you trying to achieve? (e.g. clean, high-tech, conservative, warm, flashy, etc.)

SIMPLE ELEGANT CLASSY INFORMATIVE, EASY TO USE, A REFLECTION OF THE BUSINESS ITSELF

6b) Please provide the addresses of competitors' sites, if possible:

Do not contact the client direct - all questions should go through Brightwell Venues - info@brightwellvenues.example
Updates

thanks for the designs that I have received so far. I have these general comments:

- please avoid using icons for phones or paperclips etc 
- use dummy text (one design used text from another website) 
- there won't any live social media feeds to the site
the client likes a lot of the designs that this company comes up with: 

i look forward to see some more designs

hi all, 

further to my last update, here are a few more pointers:
- there will be no search facilities - so no "search" box please 
- please just use the images supplied - no stock ones
- use just the page names give (no other pages) 

The client is looking for a simple, elegant design. 

Many thanks 
Rolf 

thanks for all the designs. 

I have uploaded another file to the brief which shows some posters that the client particularly likes. Perhaps the homepage could consist of large rectangle made up of a number of boxes - for some introductory text, a large image, mailing list, contact details, Lunch Special etc - just an idea! 
It's clear that the client likes clean lines with square edges. 
I want to be able to pass the designs directly onto the client so can designers avoid adding extra info or page. For example one design has a tab for a "Gift Card" - it will be easier for me if such additions are avoided. 

thanks!                                                                                                                                                                                                                                                                                                                                                                                                    

Thank you for all your designs - please keep them coming! 

hi all,

I am meeting the client tomorrow afternoon so please submit revisions / designs before then. 

Many thanks, 
Rolf

Target Market(s)

Business people, upmarket etc

Industry/Entity Type

Business

Requirements
Must have
• - The home page needs a slide show of images as well as:
- a mailing list form - very simple, "Join our mailing list - name, email"
- 3 or 4 sentences of text
- facebook link

```html
<!DOCTYPE html>
<html lang="en">
<head>
<meta charset="utf-8">
<title>Maplehaven Italian</title>
<link rel="stylesheet" href="https://fonts.googleapis.com/css2?family=Ubuntu:wght@300;400;500&family=Great+Vibes&display=swap">
<style>
:root{
  --wood:#2b2b2b;
  --wood-dark:#1a1a1a;
  --panel-line:#6a6a6a;
  --box-top:#2e2e2e;
  --box-bottom:#080808;
  --text:#e4e4e4;
  --muted:#b9b9b9;
  --white:#ffffff;
  --field:#3a3a3a;
}
*{margin:0;padding:0;box-sizing:border-box}
html,body{width:1020px;height:1200px;overflow:hidden}
body{
  position:relative;
  font-family:"Ubuntu",Arial,sans-serif;
  font-weight:300;
  color:var(--text);
  background:linear-gradient(90deg,var(--wood-dark),var(--wood) 20%,#323232 50%,var(--wood) 80%,var(--wood-dark));
}
.abs{position:absolute}

/* hero slideshow */
.hero{left:30px;top:7px;width:965px;height:580px;
  background:
    radial-gradient(ellipse 260px 120px at 72% 68%,rgba(240,222,205,.9),rgba(240,222,205,0) 100%),
    radial-gradient(ellipse 150px 110px at 18% 80%,rgba(235,215,200,.85),rgba(235,215,200,0) 100%),
    radial-gradient(ellipse 140px 260px at 88% 30%,rgba(200,170,150,.55),rgba(200,170,150,0) 100%),
    linear-gradient(90deg,#3a0e0a 0%,#6a2818 25%,#4a2a22 50%,#5a4038 75%,#2a1a16 100%)}
.slide-arrow{top:255px;width:22px;height:66px}
.slide-arrow.prev{left:8px}
.slide-arrow.next{left:990px}
.brand{left:30px;top:37px;width:356px;height:96px;background:rgba(255,255,255,.72);border-radius:3px;
  display:flex;align-items:center;justify-content:center}
.brand-name{font-size:34px;font-weight:400;color:#1a1a1a;letter-spacing:2px}
.phone{left:795px;top:21px;font-size:22px;font-weight:400;color:var(--white)}

/* nav */
.nav{left:45px;top:509px;width:939px;height:41px;border:1px solid #6d6d6d;border-radius:5px;
  background:linear-gradient(rgba(40,40,40,.9),rgba(10,10,10,.95));display:flex;padding-left:57px}
.nav a{font-size:12px;font-weight:400;color:#ddd;text-decoration:none;line-height:39px;padding:0 21px;border-right:1px solid #555}
.nav a:last-child{border-right:none}
.nav a.current{color:var(--white);padding-left:0}

/* content panel */
.panel{left:45px;top:560px;width:939px;height:560px;border:1px solid var(--panel-line);border-radius:6px;
  background:linear-gradient(rgba(60,60,60,.85),rgba(35,35,35,.9))}
.card{left:62px;width:227px;border:1px solid #555;border-radius:6px;
  background:linear-gradient(var(--box-top),var(--box-bottom))}
.booking{top:597px;height:75px}
.booking .badge{left:10px;top:8px;width:42px;height:58px;background:linear-gradient(#c98e5e,#6d4a3a);border-radius:4px}
.booking .line1{left:66px;top:12px;font-size:17px;color:#ddd}
.booking .line2{left:66px;top:36px;font-size:20px;font-weight:400;color:var(--white)}
.card-head{height:36px;border-bottom:1px solid #444;display:flex;align-items:center;gap:12px;padding-left:14px;font-size:14px;font-weight:400;color:var(--white)}
.dot{width:20px;height:20px;background:#b23020;border-radius:50%}
.square{width:26px;height:26px;background:linear-gradient(#cfd3e6,#5a5f7a)}
.join{top:686px;height:202px}
.field-row{position:absolute;left:0;width:210px;display:flex;align-items:center;justify-content:flex-end;gap:8px;font-size:12px;color:#ccc}
.field{width:140px;height:23px;background:var(--field);border:1px solid #444}
.submit{left:127px;top:155px;width:76px;height:30px;border:1px solid #777;border-radius:6px;
  background:linear-gradient(#2a2a2a,#000);font-size:12px;font-weight:400;color:var(--white);text-align:center;line-height:28px}
.address{top:903px;height:182px}
.address .lines{left:40px;top:48px;font-size:12px;line-height:19px;color:#ddd}
.address .contact{left:10px;top:118px;font-size:12px;line-height:19px;color:#ddd;white-space:nowrap}

.welcome-title{left:322px;top:590px;font-family:"Great Vibes",cursive;font-weight:400;font-size:40px;line-height:48px;color:var(--white);
  border-bottom:1px dotted #999;padding-right:16px}
.intro{left:341px;top:664px;width:625px;font-size:12px;line-height:22.5px;color:#e8e8e8}
.intro p+p{margin-top:22px}
.more{font-size:10px;font-weight:400;color:var(--white)}
.feature-title{font-size:14px;font-weight:400;color:var(--white);width:198px;border-bottom:1px solid #777;padding-bottom:4px}
.feature-img{width:196px;height:97px;border:1px solid #999}
.feature-text{width:220px;font-size:12px;line-height:21px;color:#bdbdbd}

.footer-social{left:60px;top:1148px;display:flex;gap:14px}
.footer-social span{width:27px;height:28px;border-radius:5px;background:linear-gradient(#9a9a9a,#5a5a5a)}
.copyright{left:378px;top:1151px;font-size:12px;color:#ccc}
.footer-brand{left:834px;top:1148px;font-size:20px;font-weight:400;color:var(--white);letter-spacing:1px}
</style>
</head>
<body>

<div class="abs hero" role="img" aria-label="Slideshow photo of the lounge with white leather sofas, candles, red curtains and tall windows"></div>
<svg class="abs slide-arrow prev" viewBox="0 0 22 66"><polyline points="20,2 2,33 20,64" fill="none" stroke="#fff" stroke-width="1.5"/></svg>
<svg class="abs slide-arrow next" viewBox="0 0 22 66"><polyline points="2,2 20,33 2,64" fill="none" stroke="#fff" stroke-width="1.5"/></svg>

<div class="abs brand"><span class="brand-name">MAPLEHAVEN</span></div>

<div class="abs phone">020 7946 0317</div>

<nav class="abs nav">
  <a class="current" href="#">WELCOME</a>
  <a href="#">OUR RESTAURANT</a>
  <a href="#">OUR MENU</a>
  <a href="#">GALLERY</a>
  <a href="#">EVENTS</a>
  <a href="#">RESERVATIOONS</a>
  <a href="#">CONTACT</a>
</nav>

<div class="abs panel"></div>

<div class="abs card booking">
  <div class="abs badge" role="img" aria-label="Booking agent illustration"></div>
  <div class="abs line1">Live bookings</div>
  <div class="abs line2">Book Now Online</div>
</div>

<div class="abs card join">
  <div class="card-head"><span class="dot"></span>JOIN US</div>
  <div class="field-row" style="top:46px">Name :<span class="field"></span></div>
  <div class="field-row" style="top:83px">Sur Name :<span class="field"></span></div>
  <div class="field-row" style="top:119px">Email :<span class="field"></span></div>
  <div class="abs submit">Submit</div>
</div>

<div class="abs card address">
  <div class="card-head" style="height:40px"><span class="square"></span>ADDRESS</div>
  <div class="abs lines">Maplehaven Italian,<br>12 Harrow Quay Walk,<br>City of London,E9 4QX</div>
  <div class="abs contact">Phone : 020 7946 0317<br>Email : info@maplehaven.example</div>
</div>

<h1 class="abs welcome-title">Welcome to Maplehaven</h1>
<div class="abs intro">
  <p>The true Italian values of passion, pride and family are at the core of Sofia and reflected in the welcome, service and most importantly, the food. Sofia believes that we do not simply eat to live but that we live to eat, and part of the pleasure is sharing our love and dedication to enjoying excellent food in good company with others.</p>
  <p>Sofia offers a menu that changes to reflect the best of the season's offerings, sustainably sourced from Italy and local producers to create timeless dishes with a contemporary twist. The ambition to share the food that Sofia has loved, cooked and eaten with her family over the years is now realised.</p>
</div>
<div class="abs more" style="left:905px;top:832px">Read More &gt;&gt;</div>

<div class="abs feature-title" style="left:344px;top:859px">Events and Private Hire</div>
<div class="abs feature-img" style="left:348px;top:893px;background:radial-gradient(ellipse at 55% 70%,#8a5a48 0%,#4a3a34 40%,#151515 85%)" role="img" aria-label="Plated salad on a dark dining table set for an event"></div>
<div class="abs feature-text" style="left:352px;top:999px">Maplehaven is a unique, elegant venue situated on the first floor of the historic Elmsworth Quay yacht club.</div>
<div class="abs more" style="left:352px;top:1069px">Read More</div>

<div class="abs feature-title" style="left:671px;top:861px">The Finest Italian Foods</div>
<div class="abs feature-img" style="left:672px;top:893px;background:radial-gradient(ellipse at 50% 60%,#c9922e 0%,#9a7a36 35%,#d8d0c8 75%,#efeae4 100%)" role="img" aria-label="Grilled polenta with salad and raspberries on a white plate"></div>
<div class="abs feature-text" style="left:673px;top:1000px">Maplehaven is a unique, elegant venue situated on the first floor of the historic Elmsworth Quay yacht club.</div>
<div class="abs more" style="left:674px;top:1070px">Read More</div>

<div class="abs footer-social" aria-label="Social links"><span></span><span></span><span></span><span></span></div>
<div class="abs copyright">Copyright © 2012 Maplehaven, All Rights Reserved</div>
<div class="abs footer-brand">MAPLEHAVEN</div>

</body>
</html>
```